CBD/HEMP website for e-commerce store

I need a CBD website for my shopify store. I am looking for a layout similar to these site ( https://quietmeadowcbd.com/ ) (https://elmridgecbd.com/) but with my logo and products. I am attaching what my logo looks like so that it helps with the design.

Target Market(s)

CBD HEMP CANNABIS

Industry/Entity Type

Cannabis

Coding

Coded - Design and coding required

Number of Pages Required

5+ page

Requirements
Nice to have
• I would like for it to have a trendy/galaxy feel

```html
<!DOCTYPE html>
<html lang="en">
<head>
<meta charset="utf-8">
<title>Starleaf CBD</title>
<link href="https://fonts.googleapis.com/css2?family=Montserrat:wght@400;500;600;700&family=Open+Sans:wght@400;600&display=swap" rel="stylesheet">
<style>
:root{
  --space:#151236;
  --space-deep:#0a0820;
  --nebula-violet:rgba(140,80,200,.30);
  --nebula-blue:rgba(70,90,190,.26);
  --nebula-rose:rgba(170,70,160,.20);
  --header:#09060f;
  --topbar:#1b1840;
  --mint:#6ef5ab;
  --mint-dark:#3fd98a;
  --white:#ffffff;
  --card:#f1f1f1;
  --badge:#333333;
  --rule:#7d7a9a;
  --magenta:#cf2f9b;
  --ink:#333333;
}
*{margin:0;padding:0;box-sizing:border-box}
html,body{width:1200px;height:4000px;overflow:hidden}
body{
  position:relative;
  font-family:"Montserrat",sans-serif;
  color:var(--white);
  background:var(--space);
}
.galaxy{
  left:0;top:196px;width:1200px;height:3804px;
  background:
    radial-gradient(ellipse 420px 300px at 760px 880px,var(--nebula-violet),transparent 70%),
    radial-gradient(ellipse 380px 260px at 220px 1300px,var(--nebula-blue),transparent 70%),
    radial-gradient(ellipse 460px 320px at 980px 1750px,var(--nebula-rose),transparent 70%),
    radial-gradient(ellipse 520px 360px at 300px 2500px,var(--nebula-violet),transparent 70%),
    radial-gradient(ellipse 420px 300px at 900px 3000px,var(--nebula-blue),transparent 70%),
    radial-gradient(ellipse 500px 340px at 600px 3550px,var(--nebula-rose),transparent 70%),
    linear-gradient(180deg,var(--space-deep),var(--space) 25%,#1b1644 55%,#141036 80%,var(--space-deep));
}
.abs{position:absolute}
.topbar{left:0;top:0;width:1200px;height:34px;background:var(--topbar);color:var(--mint-dark);font-family:"Open Sans",sans-serif;font-size:11px;text-align:center;line-height:34px}
.header{left:0;top:34px;width:1200px;height:162px;background:var(--header)}
.search{left:143px;top:78px;width:198px;height:34px;border-bottom:1px solid #444;display:flex;align-items:center;gap:12px;font-size:13px}
.brand{left:450px;top:70px;width:300px;text-align:center;font-size:34px;font-weight:700;letter-spacing:4px;color:var(--white);display:flex;justify-content:center;align-items:center;gap:12px}
.brand .dot{width:18px;height:18px;border-radius:50%;background:var(--mint)}
.icon{top:76px}
.nav{left:0;top:163px;width:1200px;display:flex;justify-content:center;gap:32px;font-size:13px;font-weight:500;padding-left:8px}
.nav .active{color:var(--mint-dark)}
.rule{left:144px;width:911px;height:1px;background:var(--rule)}
.section-title{left:144px;width:911px;text-align:center;font-size:34px;font-weight:400;color:var(--mint)}
.product{width:280px;text-align:center}
.product .img{width:280px;height:279px;background:radial-gradient(circle at 50% 55%,#cbb89a 0%,#e6e2db 30%,var(--card) 60%);position:relative}
.badge{position:absolute;left:6px;top:8px;background:var(--badge);color:#fff;font-size:12px;font-weight:600;padding:6px 10px}
.product .cat{margin-top:20px;font-size:15px;font-weight:400;color:#e6e4f2}
.product .name{margin:8px -30px 0;font-size:25px;font-weight:600;white-space:nowrap;letter-spacing:-.2px}
.product .price{margin-top:12px;font-size:15px}
.product .price s{margin-left:6px}
.banner{left:144px;top:1873px;width:911px;height:312px;background:radial-gradient(ellipse at 65% 50%,#93b957,#4e8a34 45%,#2c5a1f 90%);text-align:center}
.banner h3{margin-top:126px;font-size:25px;font-weight:500}
.banner a{display:inline-block;margin-top:10px;font-size:15px;font-weight:600;color:#fff;text-decoration:underline}
.feature-img{left:144px;top:2285px;width:455px;height:487px;background:radial-gradient(circle at 50% 60%,#6c7466,#3e463d 40%,#b9c0bb 90%)}
.detail{left:647px;top:2280px;width:408px}
.detail .cat{font-size:15px;font-weight:600}
.detail h2{margin-top:16px;font-size:26px;font-weight:600;color:var(--mint)}
.detail .price{margin-top:12px;font-size:25px;font-weight:600}
.detail .label{margin-top:26px;font-size:16px;font-weight:600}
.select{margin-top:8px;margin-left:3px;width:405px;height:47px;background:#fff;color:var(--ink);font-size:13px;display:flex;align-items:center;justify-content:space-between;padding:0 16px}
.btn{margin-left:3px;width:405px;height:46px;display:flex;align-items:center;justify-content:center;font-size:13px;color:var(--ink)}
.btn.cart{margin-top:17px;background:#fff;border:1px solid #ccc}
.btn.buy{margin-top:17px;background:var(--mint)}
.note{margin-top:20px;margin-left:3px;font-family:"Open Sans",sans-serif;font-size:10.5px;line-height:19px;color:#e8e6f5}
.share-title{margin-top:18px;margin-left:3px;font-size:16px;font-weight:600}
.shares{margin-top:6px;margin-left:3px;display:flex;gap:8px}
.shares span{background:#fff;color:#555;font-size:9px;height:26px;padding:0 12px;display:flex;align-items:center;gap:5px;border:1px solid #ccc}
.shares i{width:7px;height:7px;border-radius:50%;background:#666;display:inline-block}
.leafband{left:144px;top:3309px;width:911px;height:397px;background:radial-gradient(ellipse at 30% 40%,#2f5a2c,#163219 55%,#0c1d0e)}
.contact-box{left:388px;top:3416px;width:422px;height:175px;background:#fff;text-align:center;color:var(--ink)}
.contact-box h3{margin-top:20px;font-size:25px;font-weight:600;color:var(--magenta)}
.contact-box p{font-size:16px;line-height:24px;margin-top:12px}
.contact-box a{color:var(--ink);text-decoration:underline}
.f-head{top:3792px;font-size:25px;font-weight:600;color:var(--mint)}
.email{left:144px;top:3842px;width:286px;height:34px;border-bottom:1px solid #aaa;display:flex;justify-content:space-between;align-items:center;font-size:13px;padding:0 6px 0 12px}
.thanks{left:517px;top:3828px;width:280px;font-family:"Open Sans",sans-serif;font-size:10.5px;line-height:19px}
.social{top:3840px;width:18px;height:18px;border-radius:50%;background:#fff}
.links{left:144px;top:3919px;font-size:11px;font-family:"Open Sans",sans-serif}
.copy{left:144px;top:3947px;font-size:11px;font-family:"Open Sans",sans-serif}
.currency{left:978px;top:3926px;width:76px;height:32px;border:1px solid #888;font-size:11px;font-weight:600;display:flex;justify-content:space-between;align-items:center;padding:0 10px 0 14px}
</style>
</head>
<body>
<div class="abs galaxy" role="img" aria-label="Deep violet galaxy nebula background"></div>
<div class="abs topbar">Etiam consequat lacus a felis viverra, eget rhoncus massa ullamcorper</div>
<div class="abs header"></div>
<div class="abs search">
  <svg width="26" height="26" viewBox="0 0 26 26"><circle cx="11" cy="11" r="8" fill="none" stroke="#c23fa8" stroke-width="2"/><line x1="17" y1="17" x2="24" y2="24" stroke="#c23fa8" stroke-width="2"/></svg>
  <span>Search</span>
</div>
<div class="abs brand"><span class="dot"></span>STARLEAF</div>
<svg class="abs icon" style="left:982px" width="22" height="26" viewBox="0 0 22 26"><circle cx="11" cy="8" r="6" fill="none" stroke="#c23fa8" stroke-width="1.8"/><path d="M2 25c0-6 4-9 9-9s9 3 9 9z" fill="none" stroke="#c23fa8" stroke-width="1.8"/></svg>
<svg class="abs icon" style="left:1029px" width="26" height="26" viewBox="0 0 26 26"><path d="M2 10h22l-3 13H5z" fill="none" stroke="#c23fa8" stroke-width="1.8"/><path d="M8 10l5-7 5 7" fill="none" stroke="#c23fa8" stroke-width="1.8"/><path d="M9 13v7M13 13v7M17 13v7" stroke="#c23fa8" stroke-width="1.5"/></svg>
<nav class="abs nav"><span class="active">HOME</span><span>PRODUCTS</span><span>ABOUT</span><span>BLOG</span><span>CONTACT</span></nav>

<div class="abs" style="left:144px;top:230px;width:440px;height:558px;background:linear-gradient(135deg,#6b3a1c,#e6e1dc 45%,#c88a3a 75%,#f2f0ec)" role="img" aria-label="Amber CBD bottles, softgel capsules and dried hemp flower in a glass dish"></div>
<div class="abs" style="left:616px;top:230px;width:439px;height:558px;background:linear-gradient(160deg,#d4a782,#c89670 50%,#e2b48f)" role="img" aria-label="Hands holding a dropper over a small dish of CBD oil beside hemp leaves"></div>

<div class="abs rule" style="top:832px"></div>
<h2 class="abs section-title" style="top:862px">Maecenas tortor accumsan quam imperdiet</h2>

<div class="abs product" style="left:144px;top:941px"><div class="img" role="img" aria-label="CBD tincture bottle with dried hemp flower"><span class="badge">SOLD OUT</span></div><div class="cat">NULLAM LOREM URNA</div><div class="name">Fusce nec leo</div><div class="price">now $22.00 <s>$60.00</s></div></div>
<div class="abs product" style="left:459px;top:941px"><div class="img" role="img" aria-label="Glass dish of golden CBD oil with a hemp leaf"></div><div class="cat">SUSPENDISSE GRAVIDA</div><div class="name">Nulla in lorem at</div><div class="price">$22.00</div></div>
<div class="abs product" style="left:774px;top:941px"><div class="img" role="img" aria-label="CBD bottles, jar and capsules with a hemp leaf"></div><div class="cat">VESTIBULUM LUCTUS</div><div class="name">Nulla tristique</div><div class="price">$20.00</div></div>

<div class="abs product" style="left:144px;top:1389px"><div class="img" role="img" aria-label="CBD dropper bottle and vape pen on hemp leaves"></div><div class="cat">ALIQUAM ERAT</div><div class="name">Aliquam erat</div><div class="price">$14.00</div></div>
<div class="abs product" style="left:459px;top:1389px"><div class="img" role="img" aria-label="Small CBD bottle with a dropper above it"></div><div class="cat">DUIS ORNARE</div><div class="name">Pellentesque blandit</div><div class="price">$26.00</div></div>
<div class="abs product" style="left:774px;top:1389px"><div class="img" role="img" aria-label="Amber CBD bottle with vape pen and hemp flower"></div><div class="cat">NAM TEMPUS</div><div class="name">Phasellus conseq</div><div class="price">$16.00</div></div>

<div class="abs rule" style="top:1828px"></div>
<div class="abs banner" role="img" aria-label="Dropper releasing oil into an amber bottle over a blurred green background">
  <h3>Maecenas consequat enim mattis massa imperdiet quis</h3>
  <a>Shop Clearance</a>
</div>

<div class="abs rule" style="top:2236px"></div>
<div class="abs feature-img" role="img" aria-label="Hemp flower bud growing under greenhouse lights"></div>
<div class="abs detail">
  <div class="cat">CURABITUR VENENATIS</div>
  <h2>Etiam mattis augue</h2>
  <div class="price">$83.00</div>
  <div class="label">Amount</div>
  <div class="select"><span>$58.00</span><svg width="12" height="8" viewBox="0 0 12 8"><path d="M1 1l5 5 5-5" fill="none" stroke="#333" stroke-width="2"/></svg></div>
  <div class="btn cart">ADD TO CART</div>
  <div class="btn buy">BUY IT NOW</div>
  <p class="note">Please support your small, local businesses in these uncertain times by purchasing a gift card to spend at a later date, whether that be in store or online. We look forward to seeing you!</p>
  <div class="share-title">Share this:</div>
  <div class="shares"><span><i></i>TWEET</span><span><i></i>SHARE</span><span><i></i>PIN IT</span></div>
</div>

<div class="abs rule" style="top:2829px"></div>
<div class="abs product" style="left:144px;top:2870px"><div class="img" role="img" aria-label="CBD bottles, jar and capsules with a hemp leaf"><span class="badge">ON SALE</span></div><div class="cat">NULLA FACILISI</div><div class="name">Pellentesque convallis</div><div class="price">now $22.00 <s>$60.00</s></div></div>
<div class="abs product" style="left:459px;top:2870px"><div class="img" role="img" aria-label="Glass bottle of hemp seed oil with seeds"><span class="badge">ON SALE</span></div><div class="cat">QUISQUE ALIQUET</div><div class="name">Fusce vitae lectus</div><div class="price">now $22.00 <s>$60.00</s></div></div>
<div class="abs product" style="left:774px;top:2870px"><div class="img" role="img" aria-label="CBD dropper bottle and vape pen on hemp leaves"><span class="badge">ON SALE</span></div><div class="cat">ALIQUAM ERAT</div><div class="name">Aenean placerat</div><div class="price">now $22.00 <s>$60.00</s></div></div>

<div class="abs leafband" role="img" aria-label="Dense hemp leaves in deep green"></div>
<div class="abs contact-box">
  <h3>Proin eget congue</h3>
  <p>Maecenas vel tortor accumsan quam varius<br>imper diet vel eget elit.</p>
  <p>Aenean <a>Contact Us</a> tincidunt lectus dictum nisi</p>
</div>

<div class="abs rule" style="top:3751px"></div>
<div class="abs f-head" style="left:143px">15% off your first order</div>
<div class="abs email"><span>your@email.com</span><svg width="20" height="10" viewBox="0 0 20 10"><path d="M0 5h17M13 1l5 4-5 4" fill="none" stroke="#fff" stroke-width="2"/></svg></div>
<div class="abs f-head" style="left:517px">Thank You</div>
<p class="abs thanks">Etiam vel massa elementum, bibendum tellus venenatis, feugiat massa. Curabitur venenatis lacinia ornare. Cras sol licitudin cursus dui eu placerat</p>
<div class="abs f-head" style="left:868px">Follow Us</div>
<span class="abs social" style="left:867px"></span>
<span class="abs social" style="left:919px"></span>
<span class="abs social" style="left:974px"></span>
<span class="abs social" style="left:1035px"></span>
<div class="abs links">Search &nbsp;| &nbsp;Contact &nbsp;| &nbsp;Shipping &amp; Returns &nbsp;| &nbsp;Privacy Policy</div>
<div class="abs copy">Copyright &nbsp;© &nbsp;2020 &nbsp;Starleaf. &nbsp;All rights reserved.</div>
<div class="abs currency"><span>USD</span><svg width="8" height="5" viewBox="0 0 8 5"><path d="M1 1l3 3 3-3" fill="none" stroke="#fff" stroke-width="1.4"/></svg></div>
</body>
</html>
```